Varlomatch E-commerce Website Design

I'm looking into having my e-comm website built. We are an investment company that is investing in a private label focused on a rising sport category called Pickleball in EU market.

We will provide top quality material and acessories for players be ready to go to courts. We will have a range of: Rackets, Set of balls, Net, Lines, overgrip, water bottle, player bag.

As it´s a new sports category we would like to see an architecture that alows us to share some storytelling about the category, the brand and lead to purchase of our products.

We will position our self as an inclusive and fun brand that you can reach out to find more info about Pickleball Sport, buy your pickleball stuff and have fun. Its all about action and fun.

Target Market(s)

Europe Market

Industry/Entity Type

Pickleball (Sports)

Coding

Coded - Design and coding required

Number of Pages Required

1 page

Requirements
Must have
• E-commerce look and feel
Nice to have
• A bit of storytelling about the brand and specially the category (Pickleball).

```html
<!DOCTYPE html>
<html lang="en">
<head>
<meta charset="utf-8">
<title>Varlomatch — Pickleball Gear</title>
<link href="https://fonts.googleapis.com/css2?family=Montserrat:wght@400;500;600;700&family=Karla:wght@400;500;700&display=swap" rel="stylesheet">
<style>
:root{
  --olive:#8c8834;
  --olive-dark:#76722a;
  --blue:#1464a6;
  --navy:#1f4f7a;
  --ink:#222;
  --muted:#555;
  --card:#f3f3f3;
  --star:#f5a300;
  --footer:#262626;
  --white:#fff;
}
*{box-sizing:border-box;margin:0;padding:0}
html,body{width:1200px;height:3237px;overflow:hidden}
body{font-family:"Karla",sans-serif;color:var(--ink);background:var(--white);position:relative}
.abs{position:absolute}
a{color:inherit;text-decoration:none}

/* top bar */
.topbar{left:0;top:0;width:1200px;height:43px;background:var(--olive);color:#fff;font-size:14px}
.topbar .contact{left:112px;top:13px;display:flex;gap:22px;align-items:center}
.topbar .contact span{display:flex;gap:8px;align-items:center}
.topbar .sep{width:1px;height:18px;background:rgba(255,255,255,.5)}
.topbar .icons{right:112px;top:9px;display:flex;gap:14px}
.round-ico{width:27px;height:27px;border-radius:50%;background:#fff;display:flex;align-items:center;justify-content:center}

/* nav */
.nav{left:0;top:43px;width:1200px;height:93px;background:#fff}
.nav .menu{left:112px;top:40px;display:flex;gap:44px;font-size:15px;font-family:"Montserrat",sans-serif}
.nav .menu .active{color:var(--blue)}
.logo-bubble{left:465px;top:32px;width:257px;height:122px;background:#fff;border-radius:0 0 128px 128px/0 0 70px 70px;z-index:3;display:flex;align-items:center;justify-content:center;gap:10px}
.logo-bubble .dot{width:18px;height:18px;border-radius:50%;background:var(--olive)}
.logo-bubble .name{font-family:"Montserrat",sans-serif;font-weight:600;font-size:26px;color:var(--olive)}
.search{left:749px;top:26px;width:202px;height:42px;border:1px solid #e2e2e2;box-shadow:0 2px 6px rgba(0,0,0,.08);font-size:12px;color:#999;padding:14px 18px}
.search svg{position:absolute;right:14px;top:14px}
.login{left:984px;top:22px;width:104px;height:46px;border-radius:23px;background:linear-gradient(90deg,var(--olive),var(--navy));color:#fff;font-family:"Montserrat",sans-serif;font-weight:600;font-size:14px;display:flex;align-items:center;justify-content:center}

/* hero */
.hero{left:0;top:136px;width:1200px;height:602px;background:linear-gradient(120deg,#3a3d3a 0%,#5a5e55 30%,#6b4a45 60%,#8a4a44 100%)}
.hero .title-sm{left:110px;top:207px;color:#fff;font-family:"Montserrat",sans-serif;font-size:30px;letter-spacing:.5px}
.hero .title-lg{left:108px;top:252px;color:#fff;font-family:"Montserrat",sans-serif;font-weight:700;font-size:56px}
.btn-olive{background:var(--olive);color:#fff;font-family:"Montserrat",sans-serif;font-weight:600;font-size:15px;border-radius:24px;display:flex;align-items:center;justify-content:center}
.hero .cta{left:112px;top:342px;width:142px;height:45px}
.dots{left:576px;top:559px;display:flex;gap:6px}
.dots i{width:11px;height:11px;border-radius:50%;background:#fff}
.dots i.on{background:var(--blue)}

/* sections */
.section-title{left:0;width:1200px;text-align:center;font-family:"Montserrat",sans-serif;font-weight:500;font-size:30px;color:var(--ink)}
.card{width:232px;height:302px;background:var(--card);border-radius:4px;overflow:hidden;text-align:center}
.card.lift{background:#fff;box-shadow:0 3px 12px rgba(0,0,0,.14)}
.card .ph{height:175px;width:100%;position:relative}
.card h3{font-family:"Montserrat",sans-serif;font-weight:500;font-size:17px;margin-top:22px}
.stars{margin-top:10px;display:flex;justify-content:center;gap:2px}
.price{margin-top:10px;font-family:"Montserrat",sans-serif;font-weight:500;font-size:17px}
.price s{color:#888;margin-left:8px;font-weight:400}
.quick{position:absolute;left:50px;top:64px;width:134px;height:47px;background:#fff;display:flex;justify-content:space-around;align-items:center;border-radius:2px}
.arrow{width:51px;height:51px;border-radius:50%;display:flex;align-items:center;justify-content:center}
.arrow.light{background:#fff;box-shadow:0 2px 8px rgba(0,0,0,.15)}
.arrow.dark{background:var(--olive)}

.pills{left:111px;top:1358px;display:flex;gap:9px}
.pill{width:132px;height:41px;border:1px solid var(--olive-dark);border-radius:21px;display:flex;align-items:center;justify-content:center;font-family:"Montserrat",sans-serif;font-size:14px;color:#333}
.pill.on{background:var(--olive-dark);color:#fff}

.about{left:0;top:1462px;width:600px;height:427px;background:var(--blue);color:#fff;text-align:center}
.about h2{margin-top:92px;font-family:"Montserrat",sans-serif;font-weight:600;font-size:31px}
.about p{width:450px;margin:24px auto 0;font-size:15px;line-height:26px}
.about .shop{display:inline-flex;margin-top:28px;width:134px;height:49px;border:2px solid #fff;border-radius:25px;align-items:center;justify-content:center;font-family:"Montserrat",sans-serif;font-weight:600;font-size:15px}
.about-img{left:600px;top:1462px;width:600px;height:427px;background:linear-gradient(180deg,#3c82c9 0%,#79a8d0 35%,#3e8a55 55%,#2f7a46 100%)}

.newsletter{left:0;top:2469px;width:1200px;height:377px;background:linear-gradient(110deg,#d9dcdc,#eceeed 45%,#dcdfdb);text-align:center}
.newsletter .pre{margin-top:96px;font-family:"Montserrat",sans-serif;font-size:19px}
.newsletter .pre em{font-style:normal;color:var(--olive)}
.newsletter h2{margin-top:14px;font-family:"Montserrat",sans-serif;font-weight:500;font-size:30px}
.newsletter p{margin-top:12px;font-size:15px}
.subscribe-form{position:absolute;left:286px;top:236px;width:628px;height:53px;border:1px solid #aaa;border-radius:27px;text-align:left;padding:17px 32px;font-size:15px;color:#666}
.subscribe-form .btn-olive{position:absolute;right:-1px;top:-1px;width:165px;height:53px;border-radius:27px}

.footer{left:0;top:2846px;width:1200px;height:391px;background:var(--footer);color:#fff}
.fcol{top:83px}
.fcol h4{font-family:"Montserrat",sans-serif;font-weight:600;font-size:17px;margin-bottom:14px}
.fcol li{list-style:none;font-size:15px;line-height:26px}
.fcol .ci{display:flex;gap:14px;font-size:15px;line-height:26px;margin-bottom:16px}
.fcol .ci svg{flex:none;margin-top:5px}
.footer .rule{left:112px;top:297px;width:976px;height:1px;background:#444}
.footer .copy{left:0;top:336px;width:1200px;text-align:center;font-size:15px}
</style>
</head>
<body>

<div class="abs topbar">
  <div class="abs contact">
    <span><svg width="14" height="11" viewBox="0 0 14 11"><rect width="14" height="11" rx="1" fill="#fff"/><path d="M0 1l7 5 7-5" stroke="#8c8834" stroke-width="1.4" fill="none"/></svg>info@varlomatch.com</span>
    <i class="sep"></i>
    <span><svg width="13" height="13" viewBox="0 0 24 24"><path fill="#fff" d="M6.6 10.8a15 15 0 006.6 6.6l2.2-2.2a1 1 0 011-.25 11.4 11.4 0 003.6.57 1 1 0 011 1V20a1 1 0 01-1 1A17 17 0 013 4a1 1 0 011-1h3.5a1 1 0 011 1c0 1.25.2 2.45.57 3.57a1 1 0 01-.25 1z"/></svg>+1 (555) 014 2290</span>
  </div>
  <div class="abs icons">
    <span class="round-ico"><svg width="14" height="13" viewBox="0 0 24 22"><path fill="#8c8834" d="M12 21l-1.5-1.3C5 15 2 12.2 2 8.5A5.4 5.4 0 017.5 3 6 6 0 0112 5a6 6 0 014.5-2A5.4 5.4 0 0122 8.5c0 3.7-3 6.5-8.5 11.2z"/></svg></span>
    <span class="round-ico"><svg width="14" height="13" viewBox="0 0 24 22"><path fill="#8c8834" d="M2 2h4l3 11h10l3-8H7" /><circle cx="10" cy="18" r="2" fill="#8c8834"/><circle cx="18" cy="18" r="2" fill="#8c8834"/></svg></span>
  </div>
</div>

<div class="abs nav">
  <nav class="abs menu"><a class="active">Home</a><a>Products</a><a>About the Category</a></nav>
  <div class="abs search">Search
    <svg width="14" height="14" viewBox="0 0 14 14"><circle cx="6" cy="6" r="4.5" stroke="#666" stroke-width="2" fill="none"/><path d="M9.5 9.5L13 13" stroke="#666" stroke-width="2"/></svg>
  </div>
  <a class="abs login">LOG IN</a>
</div>
<div class="abs logo-bubble"><span class="dot"></span><span class="name">VARLOMATCH</span></div>

<section class="abs hero" role="img" aria-label="Photo of a pickleball player lunging at the net with a paddle on an outdoor court">
  <div class="abs title-sm">WELCOME TO</div>
  <div class="abs title-lg">VARLOMATCH</div>
  <a class="abs btn-olive cta">GET STARTED</a>
  <div class="abs dots"><i></i><i class="on"></i><i></i></div>
</section>

<h2 class="abs section-title" style="top:816px">OUR PRODUCTS</h2>
<a class="abs arrow light" style="left:40px;top:1034px"><svg width="12" height="18" viewBox="0 0 12 18"><path d="M9 2L3 9l6 7" stroke="#8c8834" stroke-width="2.4" fill="none"/></svg></a>
<a class="abs arrow dark" style="left:1107px;top:1034px"><svg width="12" height="18" viewBox="0 0 12 18"><path d="M3 2l6 7-6 7" stroke="#fff" stroke-width="2.4" fill="none"/></svg></a>

<article class="abs card" style="left:112px;top:908px">
  <div class="ph" role="img" aria-label="Paddles and yellow balls on a blue court" style="background:linear-gradient(90deg,#b9cc8a 0 18%,#5b86d4 18%)"></div>
  <h3>Set of Balls</h3>
  <div class="stars"><svg width="86" height="15" viewBox="0 0 86 15"><g fill="#f5a300"><path id="s" d="M7.5 0l2.2 4.8 5.3.5-4 3.6 1.2 5.1-4.7-2.7-4.7 2.7 1.2-5.1-4-3.6 5.3-.5z"/><use href="#s" x="17.5"/><use href="#s" x="35"/><use href="#s" x="52.5"/><use href="#s" x="70"/></g></svg></div>
  <div class="price">$16.00</div>
</article>
<article class="abs card lift" style="left:358px;top:908px">
  <div class="ph" role="img" aria-label="Net stretched across a pickleball court" style="background:linear-gradient(180deg,#9cc36a 0 15%,#4a6c8c 15%,#2f5272)">
    <div class="quick">
      <svg width="14" height="13" viewBox="0 0 24 22"><path fill="#555" d="M2 2h4l3 11h10l3-8H7z"/><circle cx="10" cy="18" r="2" fill="#555"/><circle cx="18" cy="18" r="2" fill="#555"/></svg>
      <svg width="16" height="14" viewBox="0 0 24 22"><path fill="#2a69b0" d="M12 21l-1.5-1.3C5 15 2 12.2 2 8.5A5.4 5.4 0 017.5 3 6 6 0 0112 5a6 6 0 014.5-2A5.4 5.4 0 0122 8.5c0 3.7-3 6.5-8.5 11.2z"/></svg>
      <svg width="16" height="10" viewBox="0 0 16 10"><ellipse cx="8" cy="5" rx="7.5" ry="4.5" fill="#333"/><circle cx="8" cy="5" r="2.3" fill="#fff"/></svg>
    </div>
  </div>
  <h3>Net</h3>
  <div class="stars"><svg width="86" height="15" viewBox="0 0 86 15"><g fill="#f5a300"><use href="#s"/><use href="#s" x="17.5"/><use href="#s" x="35"/><use href="#s" x="52.5"/><use href="#s" x="70"/></g></svg></div>
  <div class="price">$26.00<s>$17.00</s></div>
</article>
<article class="abs card" style="left:605px;top:908px">
  <div class="ph" role="img" aria-label="Two orange paddles with yellow balls on blue background" style="background:#4a88d8"></div>
  <h3>Rackets</h3>
  <div class="stars"><svg width="86" height="15" viewBox="0 0 86 15"><g fill="#f5a300"><use href="#s"/><use href="#s" x="17.5"/><use href="#s" x="35"/><use href="#s" x="52.5"/><use href="#s" x="70"/></g></svg></div>
  <div class="price">$62.00</div>
</article>
<article class="abs card" style="left:852px;top:908px">
  <div class="ph" role="img" aria-label="Rolls of black overgrip tape" style="background:linear-gradient(135deg,#e8e8e8,#cfcfcf)"></div>
  <h3>Overgrip</h3>
  <div class="stars"><svg width="86" height="15" viewBox="0 0 86 15"><g fill="#f5a300"><use href="#s"/><use href="#s" x="17.5"/><use href="#s" x="35"/><use href="#s" x="52.5"/><use href="#s" x="70"/></g></svg></div>
  <div class="price">$79.00</div>
</article>

<h2 class="abs section-title" style="top:1291px">ABOUT THE CATEGORY</h2>
<div class="abs pills">
  <a class="pill">RACKETS</a><a class="pill">SET OF BALLS</a><a class="pill on">NET</a><a class="pill">LINES</a><a class="pill">OVERGRIP</a><a class="pill">LINES</a><a class="pill">OVERGRIP</a>
</div>

<section class="abs about">
  <h2>About Net</h2>
  <p>Lorem ipsum dolor sit amet, consectetur adipiscing elit, sed do eiusmod tempor incididunt ut labore et dolore magna aliqua. Ut enim ad minim veniam, quis nostrud exercitation ullamco laboris nisi ut aliquip ex ea commodo consequat.</p>
  <a class="shop">SHOP NOW</a>
</section>
<div class="abs about-img" role="img" aria-label="Close view of a net across a green and blue outdoor court"></div>

<h2 class="abs section-title" style="top:1974px">FEATURED PRODUCTS</h2>
<a class="abs arrow light" style="left:41px;top:2192px"><svg width="12" height="18" viewBox="0 0 12 18"><path d="M9 2L3 9l6 7" stroke="#8c8834" stroke-width="2.4" fill="none"/></svg></a>
<a class="abs arrow dark" style="left:1108px;top:2192px"><svg width="12" height="18" viewBox="0 0 12 18"><path d="M3 2l6 7-6 7" stroke="#fff" stroke-width="2.4" fill="none"/></svg></a>

<article class="abs card" style="left:112px;top:2067px">
  <div class="ph" role="img" aria-label="Yellow ball resting on a court line at dusk" style="background:linear-gradient(180deg,#8a8570,#4a4a48 60%,#2e3033)"></div>
  <h3>Lines</h3>
  <div class="stars"><svg width="86" height="15" viewBox="0 0 86 15"><g fill="#f5a300"><use href="#s"/><use href="#s" x="17.5"/><use href="#s" x="35"/><use href="#s" x="52.5"/><use href="#s" x="70"/></g></svg></div>
  <div class="price">$16.00</div>
</article>
<article class="abs card lift" style="left:359px;top:2067px">
  <div class="ph" role="img" aria-label="Players resting by the net on a court" style="background:linear-gradient(180deg,#d8dbe0,#9aa4ab 55%,#c77d74)"></div>
  <h3>Water Bottle</h3>
  <div class="stars"><svg width="86" height="15" viewBox="0 0 86 15"><g fill="#f5a300"><use href="#s"/><use href="#s" x="17.5"/><use href="#s" x="35"/><use href="#s" x="52.5"/><use href="#s" x="70"/></g></svg></div>
  <div class="price">$26.00</div>
</article>
<article class="abs card" style="left:607px;top:2067px">
  <div class="ph" role="img" aria-label="Red player bag holding balls" style="background:linear-gradient(135deg,#d8352a,#e4503c 60%,#7a2a22)"></div>
  <h3>Player Bag</h3>
  <div class="stars"><svg width="86" height="15" viewBox="0 0 86 15"><g fill="#f5a300"><use href="#s"/><use href="#s" x="17.5"/><use href="#s" x="35"/><use href="#s" x="52.5"/><use href="#s" x="70"/></g></svg></div>
  <div class="price">$62.00</div>
</article>
<article class="abs card" style="left:854px;top:2067px">
  <div class="ph" role="img" aria-label="Red paddle and yellow ball on a court corner" style="background:linear-gradient(160deg,#3d6a44 0 40%,#2f3d55 40%)"></div>
  <h3>Pickleball</h3>
  <div class="stars"><svg width="86" height="15" viewBox="0 0 86 15"><g fill="#f5a300"><use href="#s"/><use href="#s" x="17.5"/><use href="#s" x="35"/><use href="#s" x="52.5"/><use href="#s" x="70"/></g></svg></div>
  <div class="price">$79.00</div>
</article>

<section class="abs newsletter" role="img" aria-label="Faded background photo of a player with a paddle">
  <div class="pre">Special <em>Offers</em> for Subscription</div>
  <h2>SIGN UP OUR NEWSLETTER</h2>
  <p>Lorem ipsum dolor sit amet, consectetur adipiscing elit, sed do.</p>
  <div class="subscribe-form">Enter email<a class="btn-olive">SUBSCRIBE</a></div>
</section>

<footer class="abs footer">
  <div class="abs fcol" style="left:112px">
    <h4>QUICK LINKS</h4>
    <ul><li>Home</li><li>About the category</li><li>Product</li><li>Contact</li></ul>
  </div>
  <div class="abs fcol" style="left:323px">
    <h4>CONTACT US</h4>
    <div class="ci"><svg width="12" height="16" viewBox="0 0 12 16"><path fill="#fff" d="M6 0a6 6 0 00-6 6c0 4.5 6 10 6 10s6-5.5 6-10a6 6 0 00-6-6zm0 8.5A2.5 2.5 0 116 3.5a2.5 2.5 0 010 5z"/></svg><span>Lorem ipsum dolor sit amet,<br>consectetur adipiscing elit</span></div>
    <div class="ci"><svg width="15" height="15" viewBox="0 0 24 24"><path fill="#fff" d="M6.6 10.8a15 15 0 006.6 6.6l2.2-2.2a1 1 0 011-.25 11.4 11.4 0 003.6.57 1 1 0 011 1V20a1 1 0 01-1 1A17 17 0 013 4a1 1 0 011-1h3.5a1 1 0 011 1c0 1.25.2 2.45.57 3.57a1 1 0 01-.25 1z"/></svg><span>+1 (555) 014 2290</span></div>
    <div class="ci"><svg width="15" height="12" viewBox="0 0 14 11"><rect width="14" height="11" rx="1" fill="#fff"/><path d="M0 1l7 5 7-5" stroke="#262626" stroke-width="1.4" fill="none"/></svg><span>info@varlomatch.com</span></div>
  </div>
  <div class="abs fcol" style="left:649px">
    <h4>COMPANY</h4>
    <ul><li>Terms &amp; Conditions</li><li>Privacy Policy</li><li>About Us</li><li>Support</li></ul>
  </div>
  <div class="abs fcol" style="left:904px">
    <h4>FOLLOW US</h4>
    <ul><li>Friendbook</li><li>Chirper</li><li>Snapgram</li><li>WorkLink</li><li>Circles Plus</li><li>ClipTube</li></ul>
  </div>
  <div class="abs rule"></div>
  <div class="abs copy">©Copyrights 2023 Varlomatch &nbsp;&nbsp;|&nbsp;&nbsp; All Rights Reserved</div>
</footer>

</body>
</html>
```